Los Brava Dip – CPG Website with WordPress - Store Locator: WP Maps plugin

Larkfield Food Company is a startup consumer packaged goods (CPG) brand launching its flagship product line — Los Brava Dip. We’re seeking a talented web designer to create a bold, professional, mobile-optimized website using WordPress with a WP Maps store locator to help customers find local retailers.

Our goal is to build a strong online presence that supports both retail growth and direct-to-consumer sales.

See Los Brava _Website_Design_Brief word document.

The website URL is https://losbravadip.example/

Target Market(s)

Consumers of gourmet salsa

Industry/Entity Type

Consumer Packaged Goods - Salsa manufacturer.

Coding

Coded - Design and coding required

Number of Pages Required

5+ page

Requirements
Must have
• The design of the Los Brava Dip website shall emulate the clean, polished aesthetic of Fennigo.example.

```html
<!DOCTYPE html>
<html lang="en">
<head>
<meta charset="utf-8">
<title>About Los Brava</title>
<link rel="stylesheet" href="https://fonts.googleapis.com/css2?family=Figtree:wght@400;500;700&family=Roboto+Condensed:wght@700&display=swap">
<style>
:root{
  --red:#c8242c;
  --red-dark:#a51c20;
  --orange:#e8821e;
  --amber:#eeae33;
  --ink:#1c1c1c;
  --card:#22160a;
  --white:#ffffff;
  --star:#f39a1a;
}
*{margin:0;padding:0;box-sizing:border-box}
html,body{width:682px;height:1200px;overflow:hidden;background:var(--white)}
body{position:relative;font-family:"Figtree",sans-serif;color:var(--ink)}
.abs{position:absolute}
.display{font-family:"Roboto Condensed",sans-serif;font-weight:700;text-transform:uppercase}
.caps{text-transform:uppercase;letter-spacing:.12em;font-weight:500}

/* header */
.site-header{left:0;top:0;width:682px;height:45px;background:var(--white);z-index:3}
.logo-badge{left:56px;top:0;width:94px;height:60px;background:var(--white);border-radius:0 0 47px 47px;z-index:3}
.brand-name{font-family:"Figtree",sans-serif;font-weight:700;color:var(--red);font-size:20px;white-space:nowrap}
.header-brand{left:67px;top:12px;z-index:4}
.main-nav{left:185px;top:19px;display:flex;gap:0;z-index:4;font-size:7.6px}
.main-nav a{position:absolute;color:var(--ink);text-decoration:none;white-space:nowrap}
.main-nav .active{border-bottom:1px solid var(--red);padding-bottom:2px}
.btn-contact{left:540px;top:14px;width:74px;height:20px;border-radius:10px;background:var(--red);color:var(--white);font-size:7.6px;display:flex;align-items:center;justify-content:center;z-index:4}

/* hero */
.hero{left:0;top:45px;width:682px;height:184px;background:linear-gradient(100deg,#f2a52a 0%,#ec8420 30%,#e5631a 50%,#a7261a 72%,#5c1410 90%,#3a1c0c 100%)}
.hero-title{left:0;top:110px;width:682px;text-align:center;color:var(--white);font-size:34px;letter-spacing:.01em}
.hero-swash{left:283px;top:150px}

/* story */
.story-photo{left:56px;top:296px;width:224px;height:224px;border-radius:50%;border:1.5px solid #d9535a;padding:6px}
.story-photo div{width:100%;height:100%;border-radius:50%;background:radial-gradient(circle at 35% 20%,#7cb33a 0%,#c8242c 40%,#e8651a 65%,#6b3a1e 100%)}
.eyebrow{color:var(--red);font-size:8.6px;border-top:1px solid var(--red);padding:2px 3px 0}
.story-eyebrow{left:297px;top:287px}
.story-heading{left:297px;top:305px;font-size:24px;color:var(--ink)}
.story-swash{left:297px;top:332px}
.copy{font-size:10.2px;line-height:15.5px;color:#2a2a2a;white-space:nowrap}
.p1{left:297px;top:350px}
.p2{left:297px;top:444px}
.p3{left:78px;top:540px}

/* reviews */
.reviews{left:0;top:634px;width:682px;height:295px;background:radial-gradient(ellipse at 50% 30%,#f0b23a 0%,#eba22f 55%,#e58f20 100%)}
.rev-eyebrow{left:0;top:667px;width:682px;text-align:center}
.rev-eyebrow span{color:var(--white);border-top:1px solid var(--white);border-bottom:1px solid var(--white);padding:2px 4px;font-size:8.6px}
.rev-heading{left:0;top:685px;width:682px;text-align:center;color:var(--white);font-size:20px}
.rev-swash{left:287px;top:711px}
.rating{left:274px;top:728px;display:flex;align-items:center;gap:3px;color:var(--white);font-size:7.2px;font-weight:700}
.card{top:764px;width:180px;height:100px;background:var(--card);border:1px solid #6b5a3e;padding:17px 20px}
.card .stars{display:flex;gap:3px;margin-bottom:8px}
.card p{color:var(--white);font-weight:700;font-size:9.4px;line-height:13px}
.c1{left:61px}.c2{left:252px}.c3{left:439px}
.arrows{left:320px;top:879px}

/* follow */
.follow{left:0;top:929px;width:682px;height:159px;background:linear-gradient(90deg,#d8461e 0%,#d43a1e 45%,#b41f20 75%,#9c1a1c 100%)}
.follow-title{left:216px;top:961px;width:230px;height:27px;border-top:1px solid rgba(255,255,255,.8);border-bottom:1px solid rgba(255,255,255,.8);text-align:center;color:var(--white);font-weight:700;font-size:16px;line-height:26px;letter-spacing:.02em}
.social{top:1010px;width:45px;height:45px;border-radius:50%;border:1.5px solid var(--white)}
.s1{left:278px}.s2{left:337px}

/* footer */
.footer-divider-v{left:168px;top:1088px;width:1px;height:112px;background:#dddddd}
.footer-divider-h{left:168px;top:1154px;width:505px;height:1px;background:#dddddd}
.footer-brand{left:42px;top:1128px;font-size:26px}
.footer-nav{left:199px;top:1124px;display:flex;align-items:center;font-size:7.8px;white-space:nowrap}
.footer-nav .dot{width:3px;height:3px;background:var(--red);margin:0 14px}
.legal{top:1170px;font-size:7.4px;color:#333;white-space:nowrap}
.mini-social{top:1165px;width:16px;height:16px;border-radius:50%;background:var(--ink)}
</style>
</head>
<body>

<header>
  <div class="abs site-header"></div>
  <div class="abs logo-badge"></div>
  <div class="abs brand-name header-brand">Los Brava</div>
  <nav class="abs main-nav caps" style="left:0;top:0">
    <a class="active" style="left:185px;top:19px">About</a>
    <a style="left:245px;top:19px">Products</a>
    <a style="left:322px;top:19px">Where to Buy</a>
    <a style="left:418px;top:19px">Recipes</a>
    <a style="left:484px;top:19px">Reviews</a>
  </nav>
  <div class="abs btn-contact caps">Contact ›</div>
</header>

<section>
  <div class="abs hero" role="img" aria-label="Abstract flame artwork in orange and deep red"></div>
  <h1 class="abs display hero-title">About Los Brava</h1>
  <svg class="abs hero-swash" width="150" height="10" viewBox="0 0 150 10"><path d="M2 8 Q20 3 75 3 T148 5" stroke="#fff" stroke-width="2.4" fill="none" stroke-linecap="round"/></svg>
</section>

<section>
  <div class="abs story-photo"><div role="img" aria-label="Photo of red chili peppers in a painted bowl with salsa and chips"></div></div>
  <div class="abs eyebrow caps story-eyebrow">Our Story</div>
  <h2 class="abs display story-heading">About Los Brava</h2>
  <svg class="abs story-swash" width="104" height="8" viewBox="0 0 104 8"><path d="M1 6 Q30 2 102 3" stroke="#c8242c" stroke-width="2.2" fill="none" stroke-linecap="round"/></svg>
  <p class="abs copy p1">Los Brava was founded in 2025 with a simple vision: to create bold,<br>premium salsas that deliver authentic flavor using real, honest<br>ingredients. What began as a homegrown recipe has grown into a<br>professionally scaled brand, built for regional retail distribution and<br>future expansion.</p>
  <p class="abs copy p2">Crafted in small batches using vine-ripened crushed tomatoes, real chili<br>pepper purees, and carefully balanced natural spices, each Los Brava<br>variety offers rich texture and depth—without fillers, preservatives, or<br>shortcuts. From the classic All Natural to the Habanero, every jar<br>reflects a commitment to quality and flavor integrity.</p>
  <p class="abs copy p3">With production based in Texas, Los Brava partners with local suppliers, regional co-packers, and independent retailers<br>to ensure consistency, freshness, and operational scalability. The company is driven by a belief that great food is rooted<br>in simplicity, and that authenticity always earns shelf space.</p>
</section>

<section>
  <div class="abs reviews" role="img" aria-label="Warm golden background with blurred salsa texture"></div>
  <div class="abs rev-eyebrow caps"><span>What People Say</span></div>
  <h2 class="abs display rev-heading">Customer Reviews</h2>
  <svg class="abs rev-swash" width="104" height="8" viewBox="0 0 104 8"><path d="M1 6 Q30 2 102 3" stroke="#c8242c" stroke-width="2.2" fill="none" stroke-linecap="round"/></svg>
  <div class="abs rating">
    <svg width="62" height="9" viewBox="0 0 62 9" fill="#fff"><g id="st"><path d="M4.5 0 L5.6 3.2 L9 3.3 L6.3 5.3 L7.3 8.6 L4.5 6.6 L1.7 8.6 L2.7 5.3 L0 3.3 L3.4 3.2Z"/></g><use href="#st" x="12"/><use href="#st" x="24"/><use href="#st" x="36"/><use href="#st" x="48"/></svg>
    <span>4.8 From 480 Reviews</span>
  </div>
  <svg width="0" height="0" style="position:absolute"><defs><path id="gs" d="M4.5 0 L5.6 3.2 L9 3.3 L6.3 5.3 L7.3 8.6 L4.5 6.6 L1.7 8.6 L2.7 5.3 L0 3.3 L3.4 3.2Z" fill="#f39a1a"/></defs></svg>
  <div class="abs card c1"><svg width="60" height="9"><use href="#gs"/><use href="#gs" x="12"/><use href="#gs" x="24"/><use href="#gs" x="36"/><use href="#gs" x="48"/></svg><p style="margin-top:8px">“Overall, I very much enjoyed the salsa. Not too hot, but just right”</p></div>
  <div class="abs card c2"><svg width="60" height="9"><use href="#gs"/><use href="#gs" x="12"/><use href="#gs" x="24"/><use href="#gs" x="36"/><use href="#gs" x="48"/></svg><p style="margin-top:8px">“Well priced. Love the heat...”</p></div>
  <div class="abs card c3"><svg width="60" height="9"><use href="#gs"/><use href="#gs" x="12"/><use href="#gs" x="24"/><use href="#gs" x="36"/><use href="#gs" x="48"/></svg><p style="margin-top:8px">“Very good, and I'm a salsa snob!”</p></div>
  <svg class="abs arrows" width="44" height="22" viewBox="0 0 44 22"><path d="M12 1 L2 11 L12 21" stroke="#fff" stroke-width="1.6" fill="none"/><path d="M31 1 L41 11 L31 21" stroke="#fff" stroke-width="1.6" fill="none"/></svg>
</section>

<section>
  <div class="abs follow" role="img" aria-label="Abstract flame artwork in red and orange"></div>
  <div class="abs follow-title caps">Follow Us On</div>
  <div class="abs social s1" aria-label="Social profile link"></div>
  <div class="abs social s2" aria-label="Social profile link"></div>
</section>

<footer>
  <div class="abs footer-divider-v"></div>
  <div class="abs footer-divider-h"></div>
  <div class="abs brand-name footer-brand">Los Brava</div>
  <nav class="abs footer-nav caps">
    <span>About</span><i class="dot"></i><span>Products</span><i class="dot"></i><span>Where to Buy</span><i class="dot"></i><span>Recipes</span><i class="dot"></i><span>Reviews</span><i class="dot"></i><span>Contact</span>
  </nav>
  <div class="abs legal" style="left:196px">© 2025 Larkfield Food Company. All rights reserved.</div>
  <div class="abs mini-social" style="left:449px" aria-label="Social profile link"></div>
  <div class="abs mini-social" style="left:469px" aria-label="Social profile link"></div>
  <div class="abs legal" style="left:499px">Privacy Policy</div>
  <div class="abs legal" style="left:555px">Terms of Use</div>
</footer>

</body>
</html>
```